Financial investment calculator report for real estae - layout & design

I am looking to Create a web report utilizing the attached information. It is an investment calculator report that will be customized report based on an online calculator. Therefore the report will need to be designed in a manner that a backend developer will be able to build off of.

The report will need to be web based but also printed in PDF format. The report will need to include the calculation format as well as be templeted to add a report user unique profile information like Headshot, Business Logo, Name, Telephone number, email etc.

The report should be modern and clean and easy to read and use a modern clean template design. It should be able to be easily color customized by the end user to produce templets in Red, Blue, Green, and Greyscale.

The report should be no more than 3 pages total with out breaking up the sections.

Section One - Cover sheet including agent bio info, Report Title and property address (both prominent), 400 Character space for property description, Property Pictures (3), and a google Maps integration image showing property location, It should also have room for about 100 words for a text disclaimer. (I will provide text soon)

Section Two - Inputs from the calculator

Section 3 - The Four Benefits & Rates of Return

Once I have a completed/approved form I will have about a half dozen forms/reports that will need to be laid out with a similar aesthetic.

Feel free to ask me any questions. Thank You
Milo

Target Market(s)

This report will be produced by real estate agents forvtheir investor clients. It should denote professionalism

Font styles to use
Sans Serif

Colors
0054AA
0677BA
7BADD7
CADEEF
E8F1F8
00AB8E
00BBA5
67D7C9
C6EFE9
E9F9F6
EB3D1F
EC4F4E
F09395
F8D3D4
FCEDEE

```html
<!DOCTYPE html>
<html lang="en">
<head>
<meta charset="utf-8">
<title>Investment Report – Data from Calculator</title>
<link href="https://fonts.googleapis.com/css2?family=Archivo:wght@400;500;600;700;800&display=swap" rel="stylesheet">
<style>
  :root {
    --brand: #a81f25;
    --brand-tint: #f3e1dc;
    --ink: #1f1f1f;
    --muted: #4a4a4a;
    --rule: #dcdcdc;
    --page: #ffffff;
  }
  * { box-sizing: border-box; margin: 0; padding: 0; }
  html, body { width: 929px; height: 1200px; overflow: hidden; background: var(--page); }
  body { position: relative; font-family: "Archivo", Arial, sans-serif; color: var(--ink); }

  .report-header {
    position: absolute; left: 0; top: 0; width: 929px; height: 91px;
    background: var(--brand); color: #fff;
  }
  .report-header .stamp { position: absolute; top: 10px; font-size: 10px; color: #2a0a0b; }
  .report-header .stamp.date { left: 8px; }
  .report-header .stamp.title { right: 24px; }
  .brand-mark { position: absolute; left: 62px; top: 36px; display: flex; align-items: center; gap: 8px; }
  .brand-mark .dot { width: 36px; height: 36px; border: 2px solid #fff; border-radius: 50%; }
  .brand-mark .name { font-size: 15px; font-weight: 600; color: #fff; }

  .page-title { position: absolute; left: 75px; top: 128px; font-size: 37px; font-weight: 700; color: var(--brand); letter-spacing: -0.3px; }
  .page-subtitle { position: absolute; left: 76px; top: 176px; font-size: 19px; color: var(--muted); }

  .calc-table {
    position: absolute; left: 79px; width: 772px;
    border-collapse: collapse; table-layout: fixed;
    border: 1px solid var(--rule); font-size: 11px;
  }
  .calc-table td { height: 22px; padding: 0 10px; border: 1px solid var(--rule); white-space: nowrap; }
  .calc-table .section-head td {
    height: 29px; background: var(--brand-tint); font-weight: 600; font-size: 13px; color: #3a2a28;
  }
  .calc-table .total td {
    height: 29px; background: var(--brand-tint); font-weight: 700; font-size: 13px; color: #3a2a28;
  }
  .calc-table .spacer td { height: 8px; }

  .financing { top: 248px; }
  .depreciation { top: 539px; }
  .income { top: 744px; }
  .expenses { top: 900px; }

  .report-footer { position: absolute; left: 8px; right: 24px; top: 1175px; font-size: 10px; display: flex; justify-content: space-between; color: #222; }
</style>
</head>
<body>
  <header class="report-header">
    <span class="stamp date">08/08/23 10:34 AM</span>
    <span class="stamp title">Investment Report</span>
    <div class="brand-mark"><span class="dot"></span><span class="name">Larkfield</span></div>
  </header>

  <h1 class="page-title">A: Data from Calculator</h1>
  <p class="page-subtitle">Lorem Ipsum sit amet.</p>

  <table class="calc-table financing">
    <colgroup><col style="width:319px"><col style="width:128px"><col style="width:166px"><col style="width:159px"></colgroup>
    <tr class="section-head"><td colspan="4">Property Address: 318 Linwood</td></tr>
    <tr><td>Financing</td><td>20% Down</td><td>20 Year Conventional</td><td></td></tr>
    <tr><td>Purchase Price</td><td></td><td></td><td>$1690000</td></tr>
    <tr><td>Down Payment (Cash Invested)</td><td></td><td></td><td>$338000</td></tr>
    <tr><td>Amount Financed</td><td></td><td></td><td>$1352000</td></tr>
    <tr><td>Needed Capital Improvements Est.</td><td></td><td></td><td>$0</td></tr>
    <tr><td>Est. Closing Costs</td><td></td><td></td><td>$3000</td></tr>
    <tr><td>CASH Invested (Down Pmt. + Closing Costs)</td><td></td><td></td><td>$341000</td></tr>
    <tr><td></td><td>Rate</td><td>Terms (yrs)</td><td></td></tr>
    <tr><td></td><td>7%</td><td>20</td><td></td></tr>
    <tr class="total"><td colspan="3">Monthly P&amp;I</td><td>$10482</td></tr>
  </table>

  <table class="calc-table depreciation">
    <colgroup><col style="width:218px"><col style="width:120px"><col style="width:144px"><col style="width:131px"><col style="width:159px"></colgroup>
    <tr class="section-head"><td colspan="5">Depreciation (first year): (assumes 80%/20%)</td></tr>
    <tr><td></td><td></td><td>Est; Value</td><td>Yearly Rate</td><td></td></tr>
    <tr><td>Land Cost:</td><td>0 years</td><td>$338000</td><td>0%</td><td>$0</td></tr>
    <tr><td>Personal Property Cost</td><td>5 years</td><td>$45000</td><td>20%</td><td>$9000</td></tr>
    <tr><td>Building Cost: 27.5 Years</td><td>27.5 years</td><td>$1262000</td><td>3.48%</td><td>$43918</td></tr>
    <tr><td>Land Improvement Cost</td><td>15 years</td><td>$45000</td><td>5%</td><td>$2250</td></tr>
    <tr class="total"><td colspan="4">Total Depreciation</td><td>$55168</td></tr>
  </table>

  <table class="calc-table income">
    <colgroup><col style="width:229px"><col style="width:384px"><col style="width:159px"></colgroup>
    <tr class="section-head"><td colspan="3">Income</td></tr>
    <tr><td>Annual Rent</td><td></td><td>$170000</td></tr>
    <tr><td>Other Income</td><td></td><td>$0</td></tr>
    <tr><td>Less Vacancy</td><td>est. 5% of annual rent</td><td>$0</td></tr>
    <tr class="total"><td colspan="2">Gross Operating</td><td>$170000</td></tr>
  </table>

  <table class="calc-table expenses">
    <colgroup><col style="width:229px"><col style="width:384px"><col style="width:159px"></colgroup>
    <tr class="section-head"><td colspan="3">Expenses</td></tr>
    <tr><td>Real Estate Tax</td><td></td><td>$27439</td></tr>
    <tr><td>Insurance: est. $349</td><td></td><td>$3492</td></tr>
    <tr><td>Association Dues/HOA's</td><td>est. 5% of annual rent</td><td>$0</td></tr>
    <tr><td>Management</td><td></td><td>$0</td></tr>
    <tr><td>Utilities</td><td></td><td>$9192</td></tr>
    <tr><td>Advertising</td><td></td><td>$0</td></tr>
    <tr><td>Maintnence</td><td></td><td>$0</td></tr>
    <tr><td>Miscellaneous1</td><td></td><td>$0</td></tr>
    <tr class="spacer"><td></td><td></td><td></td></tr>
    <tr class="total"><td colspan="2">Total Expenses</td><td>$40123</td></tr>
  </table>

  <footer class="report-footer">
    <span>https://www.investcalcs.net/report/pdf/5</span>
    <span>2/3</span>
  </footer>
</body>
</html>
```